KLV Plant Services

We are a heavy diesel mechanical business with additional air con certificates, remapping engine rebuilt

Contact Information for Business Card

Company Name, Director Name, Managing Director, Contact details, email and website

Font styles to use
Serif
Script

```html
<!DOCTYPE html>
<html lang="en">
<head>
<meta charset="utf-8">
<title>KLV Plant Services – Business Card</title>
<link href="https://fonts.googleapis.com/css2?family=Jost:wght@400;500;700&display=swap" rel="stylesheet">
<style>
  :root {
    --navy-deep: #05063a;
    --navy: #1b1a6b;
    --accent-blue: #1f6fd6;
    --band-black: #0b0b0d;
    --paper: #ffffff;
    --paper-shade: #e9e9ec;
    --page-bg: #d9d6d1;
    --text-light: #ffffff;
  }
  * { margin: 0; padding: 0; box-sizing: border-box; }
  html, body { width: 1200px; height: 900px; overflow: hidden; }
  body {
    background: var(--page-bg);
    font-family: "Jost", sans-serif;
    position: relative;
  }
  .card {
    position: absolute;
    left: 250px;
    width: 700px;
    height: 400px;
    border-radius: 36px;
    overflow: hidden;
    box-shadow: 0 6px 18px rgba(0,0,0,0.25);
  }
  .card--front {
    top: 35px;
    background: linear-gradient(115deg, var(--navy-deep) 0%, var(--navy) 45%, var(--navy-deep) 100%);
    display: flex;
    align-items: center;
    justify-content: center;
  }
  .card--back { top: 465px; background: var(--paper); }
  .brand-name {
    font-family: "Jost", sans-serif;
    font-weight: 700;
    font-size: 44px;
    letter-spacing: 0.5px;
    display: flex;
    align-items: center;
    gap: 14px;
  }
  .brand-name__dot { width: 22px; height: 22px; border-radius: 50%; flex: none; }
  .card--front .brand-name { color: var(--text-light); }
  .card--front .brand-name__dot { background: var(--text-light); }
  .back-art { position: absolute; inset: 0; }
  .card--back .brand-name {
    position: absolute;
    right: 48px;
    top: 118px;
    color: var(--navy);
    font-size: 36px;
    line-height: 1.1;
  }
  .card--back .brand-name__dot { background: var(--navy); width: 18px; height: 18px; }
  .contact-block {
    position: absolute;
    left: 36px;
    top: 172px;
    color: var(--text-light);
  }
  .contact-block__name {
    color: var(--accent-blue);
    font-weight: 500;
    font-size: 24px;
    letter-spacing: 1px;
    text-transform: uppercase;
    line-height: 1;
  }
  .contact-block__role { font-size: 16px; margin-top: 4px; margin-left: 14px; }
  .contact-list {
    list-style: none;
    margin-top: 24px;
    margin-left: 36px;
    font-size: 15px;
    line-height: 1.45;
  }
  .contact-list li { display: flex; align-items: flex-start; gap: 10px; }
  .contact-list svg { width: 14px; height: 14px; margin-top: 4px; flex: none; fill: var(--accent-blue); }
</style>
</head>
<body>

<section class="card card--front" aria-label="Business card front">
  <div class="brand-name"><span class="brand-name__dot"></span>KLV Plant Services</div>
</section>

<section class="card card--back" aria-label="Business card back">
  <svg class="back-art" viewBox="0 0 700 400" aria-hidden="true">
    <defs>
      <linearGradient id="paperShade" x1="0" y1="0" x2="1" y2="1">
        <stop offset="0" stop-color="var(--paper-shade)"/>
        <stop offset="0.6" stop-color="var(--paper)"/>
      </linearGradient>
      <linearGradient id="navyPanel" x1="0" y1="0" x2="1" y2="1">
        <stop offset="0" stop-color="var(--navy)"/>
        <stop offset="1" stop-color="var(--navy-deep)"/>
      </linearGradient>
    </defs>
    <rect width="700" height="400" fill="url(#paperShade)"/>
    <ellipse class="back-art__band" cx="40" cy="470" rx="440" ry="420" fill="var(--band-black)"/>
    <ellipse class="back-art__gap" cx="28" cy="470" rx="418" ry="400" fill="var(--paper-shade)"/>
    <ellipse class="back-art__panel" cx="20" cy="470" rx="410" ry="392" fill="url(#navyPanel)"/>
  </svg>

  <div class="contact-block">
    <p class="contact-block__name">Daniel Morrow</p>
    <p class="contact-block__role">Managing Director</p>
    <ul class="contact-list">
      <li><svg viewBox="0 0 24 24"><path d="M6.6 10.8a15.1 15.1 0 0 0 6.6 6.6l2.2-2.2a1 1 0 0 1 1-.25 11.4 11.4 0 0 0 3.6.57 1 1 0 0 1 1 1V20a1 1 0 0 1-1 1A17 17 0 0 1 3 4a1 1 0 0 1 1-1h3.5a1 1 0 0 1 1 1c0 1.25.2 2.45.57 3.57a1 1 0 0 1-.25 1z"/></svg>0400 555 219</li>
      <li><svg viewBox="0 0 24 24"><path d="M2 5h20v14H2zm2 2v.5l8 5 8-5V7l-8 5z"/></svg>admin@klvplantservices.net</li>
      <li><svg viewBox="0 0 24 24"><path d="M12 2a10 10 0 1 0 0 20 10 10 0 0 0 0-20zm6.9 9h-3a15 15 0 0 0-1.4-6A8 8 0 0 1 18.9 11zM12 4c.9 1.2 1.8 3.6 1.9 7h-3.8C10.2 7.6 11.1 5.2 12 4zM9.5 5a15 15 0 0 0-1.4 6h-3A8 8 0 0 1 9.5 5zm-4.4 8h3a15 15 0 0 0 1.4 6 8 8 0 0 1-4.4-6zM12 20c-.9-1.2-1.8-3.6-1.9-7h3.8c-.1 3.4-1 5.8-1.9 7zm2.5-1a15 15 0 0 0 1.4-6h3a8 8 0 0 1-4.4 6z"/></svg>www.klvplantservices.net</li>
      <li><svg viewBox="0 0 24 24"><path d="M12 2a7 7 0 0 0-7 7c0 5 7 13 7 13s7-8 7-13a7 7 0 0 0-7-7zm0 9.5A2.5 2.5 0 1 1 12 6.5a2.5 2.5 0 0 1 0 5z"/></svg>48 Ridgeway Road, Hillsford<br>WA 6100, Australia</li>
    </ul>
  </div>

  <div class="brand-name"><span class="brand-name__dot"></span><span>KLV Plant<br>Services</span></div>
</section>

</body>
</html>
```